Clear Path Keystone Realty yard sign Logo

UPDATE Design logo for Realty yard sign. 24x24 diamond or 36x24 Rectangle.
Open to all ideas. We are a discount firm but want to project a high end feel. We provide 100% of all services and extensive marketing for 1/2 the fee.
The following info must be on sign
CLEAR PATH KEYSTONE (OR K) REALTY
Doran Pike 547-6093
KeystonePX.com

Target Market(s)

home sellers and buyers

Industry/Entity Type

Real Estate yard sign please see sign attached in gif

Logo Text

Clear Path Keystone Realty OR (K IN PLACE OF KEYSTONE)

Requirements
Must have
• CLEAR PATH KEYSTONE (OR K) REALTY Doran Pike 547-6093 KeystonePX.com FOR SALE (optional)

```html
<!DOCTYPE html>
<html lang="en">
<head>
<meta charset="UTF-8">
<title>Clear Path Keystone Realty – Yard Sign</title>
<link rel="stylesheet" href="https://fonts.googleapis.com/css2?family=Cinzel:wght@700&family=Arimo:wght@700&display=swap">
<style>
  :root {
    --brand-blue: #1a64a8;
    --brand-green: #8da43c;
    --sign-white: #ffffff;
    --shadow: rgba(0, 0, 0, 0.35);
  }
  html, body {
    margin: 0;
    padding: 0;
    width: 1176px;
    height: 1200px;
    overflow: hidden;
    background: var(--sign-white);
  }
  .yard-sign {
    position: relative;
    width: 1176px;
    height: 1200px;
  }
  .diamond-frame {
    position: absolute;
    inset: 0;
    filter: drop-shadow(4px 5px 3px var(--shadow));
  }
  .brand-mark {
    position: absolute;
    left: 0;
    width: 100%;
    top: 290px;
    display: flex;
    flex-direction: column;
    align-items: center;
  }
  .brand-mark__dot {
    width: 150px;
    height: 150px;
    border-radius: 50%;
    background: var(--brand-green);
    margin-bottom: 44px;
  }
  .brand-name {
    margin: 0;
    font-family: "Cinzel", serif;
    font-weight: 700;
    font-size: 62px;
    line-height: 1.12;
    color: var(--brand-blue);
    text-align: center;
    letter-spacing: 1px;
  }
  .contact {
    position: absolute;
    left: 0;
    width: 100%;
    text-align: center;
    font-family: "Arimo", sans-serif;
    font-weight: 700;
    margin: 0;
  }
  .contact--agent {
    top: 698px;
    font-size: 60px;
    color: var(--brand-blue);
    text-shadow: 3px 4px 3px var(--shadow);
  }
  .contact--web {
    top: 780px;
    font-size: 43px;
    color: var(--brand-green);
    text-shadow: 2px 3px 3px var(--shadow);
  }
</style>
</head>
<body>
  <main class="yard-sign">
    <svg class="diamond-frame" width="1176" height="1200" viewBox="0 0 1176 1200" aria-hidden="true">
      <polygon points="588,122 1066,596 588,1078 110,596"
               fill="none" stroke="var(--brand-blue)" stroke-width="15" stroke-linejoin="miter"/>
    </svg>

    <div class="brand-mark">
      <span class="brand-mark__dot" aria-hidden="true"></span>
      <p class="brand-name">CLEAR PATH<br>KEYSTONE REALTY</p>
    </div>

    <p class="contact contact--agent">Doran Pike 547-6093</p>
    <p class="contact contact--web">KeystonePX.com</p>
  </main>
</body>
</html>
```